BOLD & MINIMALIST DESIGN NEEDED

We want a very bold but minimalistic business card design that is impactful and utilizes both sides of the business card. Our current logo is included for your use.

We want bold fonts and good use of negative space. We don't want the logo to overpower the design.

Target Market(s)

Professionals who are building new commercial buildings.

Industry/Entity Type

Construction

Contact Information for Business Card

Name, Title, email, office phone, cell phone, website

Font styles to use
Serif
Sans Serif

Requirements
Must have
• Bold design!

```html
<!DOCTYPE html>
<html lang="en">
<head>
<meta charset="utf-8">
<title>Ridgeline Business Card</title>
<link rel="stylesheet" href="https://fonts.googleapis.com/css2?family=Montserrat:wght@700;800&family=Poppins:wght@300;400&display=swap">
<style>
  :root {
    --backdrop: #1d1d1f;
    --card-black: #0b0b0c;
    --paper-white: #ffffff;
    --brand-green: #8cc63f;
    --ink-black: #111111;
    --emboss-grey: #2e2e30;
    --text-light: #f2f2f2;
  }
  * { box-sizing: border-box; margin: 0; padding: 0; }
  html, body {
    width: 1200px; height: 1015px; overflow: hidden;
    background: var(--backdrop);
  }
  .canvas {
    position: relative; width: 1200px; height: 1015px;
    display: flex; flex-direction: column; align-items: center; justify-content: center;
    gap: 44px;
  }
  .card {
    position: relative; width: 760px; height: 434px;
    background: var(--card-black); overflow: hidden;
    box-shadow: 0 18px 40px rgba(0,0,0,.55);
  }
  /* Back side */
  .card-back .brand {
    position: absolute; right: 70px; top: 50%; transform: translateY(-50%);
    display: flex; align-items: center; gap: 22px;
  }
  .card-back .brand-mark {
    width: 46px; height: 46px; background: var(--brand-green);
  }
  .card-back .brand-name {
    font-family: "Montserrat", sans-serif; font-weight: 800;
    font-size: 64px; letter-spacing: 1px; color: var(--emboss-grey);
  }
  /* Front side */
  .card-front .shape { position: absolute; inset: 0; }
  .card-front .brand {
    position: absolute; left: 445px; top: 140px;
    display: flex; align-items: center; gap: 14px;
  }
  .card-front .brand-mark {
    width: 30px; height: 30px; background: var(--brand-green);
  }
  .card-front .brand-name {
    font-family: "Montserrat", sans-serif; font-weight: 800;
    font-size: 44px; color: var(--ink-black); letter-spacing: .5px;
  }
  .person {
    position: absolute; left: 58px; top: 96px;
  }
  .person-name {
    font-family: "Montserrat", sans-serif; font-weight: 800;
    font-size: 26px; color: var(--text-light); text-transform: uppercase; letter-spacing: .5px;
  }
  .person-title {
    font-family: "Poppins", sans-serif; font-weight: 400;
    font-size: 16px; color: var(--brand-green); text-transform: uppercase; margin-top: 2px;
  }
  .contact-list {
    position: absolute; left: 58px; bottom: 40px; list-style: none;
  }
  .contact-list li {
    display: flex; align-items: center; gap: 12px;
    font-family: "Poppins", sans-serif; font-weight: 300;
    font-size: 18px; line-height: 32px; color: var(--text-light);
  }
  .contact-list svg { width: 20px; height: 20px; flex: none; }
</style>
</head>
<body>
<main class="canvas">
  <section class="card card-back" aria-label="Card back">
    <div class="brand">
      <span class="brand-mark"></span>
      <span class="brand-name">RIDGELINE</span>
    </div>
  </section>

  <section class="card card-front" aria-label="Card front">
    <svg class="shape" viewBox="0 0 760 434" aria-hidden="true">
      <ellipse cx="600" cy="110" rx="285" ry="262" fill="var(--paper-white)"/>
      <path d="M312 20 A300 270 0 0 0 700 370" fill="none" stroke="var(--brand-green)" stroke-width="5" stroke-linecap="round"/>
    </svg>

    <div class="brand">
      <span class="brand-mark"></span>
      <span class="brand-name">RIDGELINE</span>
    </div>

    <div class="person">
      <h1 class="person-name">Marcus Hale</h1>
      <p class="person-title">Managing Director</p>
    </div>

    <ul class="contact-list">
      <li>
        <svg viewBox="0 0 24 24" fill="var(--brand-green)"><path d="M6.6 10.8a15 15 0 0 0 6.6 6.6l2.2-2.2c.3-.3.7-.4 1-.2 1.1.4 2.3.6 3.6.6.6 0 1 .4 1 1V20c0 .6-.4 1-1 1A17 17 0 0 1 3 4c0-.6.4-1 1-1h3.5c.6 0 1 .4 1 1 0 1.3.2 2.5.6 3.6.1.3 0 .7-.2 1z"/></svg>
        044-555 010 200
      </li>
      <li>
        <svg viewBox="0 0 24 24" fill="none" stroke="var(--brand-green)" stroke-width="2"><rect x="6" y="2" width="12" height="20" rx="2"/><line x1="11" y1="18" x2="13" y2="18"/></svg>
        044-555 010 201
      </li>
      <li>
        <svg viewBox="0 0 24 24" fill="none" stroke="var(--brand-green)" stroke-width="2"><rect x="2" y="5" width="20" height="14"/><path d="M2 5l10 8 10-8"/></svg>
        info@ridgelinebuild.com
      </li>
      <li>
        <svg viewBox="0 0 24 24" fill="none" stroke="var(--brand-green)" stroke-width="2"><circle cx="12" cy="12" r="10"/><ellipse cx="12" cy="12" rx="4" ry="10"/><line x1="2" y1="12" x2="22" y2="12"/></svg>
        www.ridgelinebuild.com
      </li>
    </ul>
  </section>
</main>
</body>
</html>
```